Business card for Sports Apparel business

DOUBLE SIDED DESIGN
We need business cards for a new sports apparel business. We are developing a protective headband for soccer initially.
Torvalle is focused on designing and developing head protection products to reduce the likelihood of concussion when playing sports. Exploring and understanding medical insights, material science research, current and former players experiences and governing bodies guidelines has allowed Torvalle to develop the safety, style, form and function requirements of a suitable product to bring to market.
Target Market(s)
Mums buying kits for the sons and daughters. Amateur footballers.
Industry/Entity Type
Sporting Good
Contact Information for Business Card
Martin Ashworth - CEO
Mobile: +44 7431589027
Email: martin@torvalle.co.uk
Tel: 0208 5519372
Helena Pargeter - COO
Mob: +44 7385 640117
Email: helena@torvalle.co.uk
Tel: 0208 5519372
Duncan Farrow - CCO
Mob: +44 7564 293081
Email: duncan@torvalle.co.uk
Tel: 0208 5519372
Look and feel
Each slider illustrates characteristics of the customer's brand and the style your logo design should communicate.

```html
<!DOCTYPE html>
<html lang="en">
<head>
<meta charset="utf-8">
<title>Torvalle Business Card</title>
<link href="https://fonts.googleapis.com/css2?family=Arimo:wght@400;700&family=Raleway:wght@700&display=swap" rel="stylesheet">
<style>
  :root {
    --backdrop: #7b4b24;
    --card-blue: #035d92;
    --card-white: #ffffff;
    --ink-light: #ffffff;
    --ink-grey: #5b5b5d;
    --card-shadow: rgba(0, 0, 0, 0.45);
  }
  html, body {
    margin: 0;
    padding: 0;
    width: 1200px;
    height: 900px;
    overflow: hidden;
    background: var(--backdrop);
  }
  .canvas {
    position: relative;
    width: 1200px;
    height: 900px;
  }
  .card {
    position: absolute;
    box-shadow: 3px 4px 6px var(--card-shadow);
  }
  .card-front {
    left: 330px;
    top: 90px;
    width: 555px;
    height: 343px;
    background: var(--card-blue);
    color: var(--ink-light);
    font-family: "Arimo", Arial, sans-serif;
    text-align: center;
  }
  .card-back {
    left: 330px;
    top: 469px;
    width: 559px;
    height: 343px;
    background: var(--card-white);
    display: flex;
    align-items: center;
    justify-content: center;
  }
  .contact-block {
    position: absolute;
    left: 0;
    right: 0;
    top: 66px;
  }
  .person-name {
    font-family: "Raleway", Arial, sans-serif;
    font-weight: 700;
    font-size: 20px;
    line-height: 22px;
    margin: 0;
    letter-spacing: 0.2px;
  }
  .person-role {
    font-size: 16px;
    line-height: 18px;
    margin: 0;
  }
  .divider {
    width: 136px;
    height: 1px;
    background: var(--ink-light);
    margin: 10px auto 13px;
  }
  .divider-lower {
    margin: 12px auto 17px;
  }
  .contact-list {
    list-style: none;
    margin: 0;
    padding: 0;
    font-size: 16.5px;
    line-height: 20.3px;
  }
  .contact-list b { font-weight: 700; }
  .address {
    font-size: 16.5px;
    line-height: 20px;
    margin: 0;
    font-style: normal;
  }
  .brand {
    display: flex;
    align-items: center;
    gap: 12px;
    font-family: "Arimo", Arial, sans-serif;
    font-weight: 400;
    font-size: 44px;
    color: var(--ink-grey);
    letter-spacing: 1px;
    margin-top: 4px;
  }
  .brand-square {
    width: 26px;
    height: 26px;
    background: var(--card-blue);
  }
</style>
</head>
<body>
<main class="canvas">
  <section class="card card-front" aria-label="Card front with contact details">
    <div class="contact-block">
      <h1 class="person-name">NATHAN ELLERY</h1>
      <p class="person-role">Managing Director</p>
      <div class="divider"></div>
      <ul class="contact-list">
        <li><b>P:</b> 020-555 018 247</li>
        <li><b>M:</b> 077-555 013 964</li>
        <li><b>E:</b> info@cardname.example</li>
        <li><b>W:</b> www.sitename.example</li>
      </ul>
      <div class="divider divider-lower"></div>
      <address class="address">12345, Address Goes Here<br>Country Name, 123456.</address>
    </div>
  </section>

  <section class="card card-back" aria-label="Card back with brand name">
    <div class="brand">
      <span class="brand-square"></span>
      <span class="brand-name">TORVALLE</span>
    </div>
  </section>
</main>
</body>
</html>
```